Payment company requires web design

We need a web design for a new company based in Singapore.

The company focuses on providing 2 key products: 1) an alternative payment option (i.e. like quib or trelloquin options) on the traditional checkout process 2) a replacement/outsource of a merchants payment page. Key in the UX flow is a end customer dashboard that manages all payments.

We look to provide a simple, fluid and easy to use payment process. The dashboard is minimalistic that allows easy navigation, review of transactions and all available options through gamification.

The final design should communicate ease of use, flexibility and transparency.

Target Market(s)

The value is for the merchant - retail/travel/insurance companies. However its the merchant's end customers that are the target and who the UX is built for.

Industry/Entity Type

It Company

Logo Text

zelnar

Number of Pages Required

5+ page

Colors
ec1f27

Requirements
Must have
• 7 pages mimicking UX flow
• payment page * 2 - 1) alternative payment type 2) outsource of merchants payment page to our business
• our landing page
• end customer verification page
• end customer registration
• customer dashboard
• UX flow in attached file
Nice to have
• open to ideas
• have asked for the logo to be added
• logo to have the colour red (chinese for prosperity)
• the company is all about flexibility, transparency in personal finance management with the option of instalment payments

```html
<!DOCTYPE html>
<html lang="en">
<head>
<meta charset="utf-8">
<title>Zelnar — Payment Processing Company</title>
<link rel="stylesheet" href="https://fonts.googleapis.com/css2?family=Open+Sans:wght@400;600;700&display=swap">
<style>
:root{
  --red:#ec1f27;
  --hero:#f87174;
  --ink:#333333;
  --muted:#555555;
  --dark-icon:#3f3f3f;
  --grey-band:#ebebeb;
  --dark-band:#3a3837;
  --white:#ffffff;
  --map:#f1f0ec;
}
*{box-sizing:border-box;margin:0;padding:0}
html,body{width:706px;height:1200px;overflow:hidden}
body{font-family:"Open Sans",Arial,sans-serif;color:var(--ink);background:var(--white);position:relative}
.abs{position:absolute}

/* Header */
.top-rule{left:0;top:0;width:706px;height:2px;background:var(--red)}
.brand{display:flex;align-items:center;gap:8px;font-weight:700;font-size:22px;color:var(--red);letter-spacing:.5px}
.brand-mark{width:22px;height:22px;background:var(--dark-icon)}
.site-brand{left:57px;top:39px}
.search{left:324px;top:15px;width:127px;height:22px;border:1px solid #333;font-size:9px;padding:5px 6px;color:#444}
.search svg{position:absolute;right:5px;top:5px}
.btn-top{top:15px;height:22px;font-size:8.5px;font-weight:700;display:flex;align-items:center;justify-content:center;border-radius:2px}
.btn-later{left:455px;width:62px;border:1px solid #333;color:#222}
.btn-buy{left:521px;width:62px;background:#4a4a4a;color:#fff}
.btn-register{left:587px;width:60px;background:var(--red);color:#fff}
.nav{top:53px;left:255px;display:flex;align-items:center;gap:0;font-size:9px;font-weight:600;color:#222}
.nav span{padding:4px 7px;margin-right:9px}
.nav .active{border:1.5px solid var(--red);color:var(--red)}

/* Hero */
.hero{left:0;top:84px;width:706px;height:302px;background:var(--hero)}
.hero-title{left:57px;top:137px;color:#fff;font-weight:600;font-size:23px;line-height:35px}
.hero-text{left:58px;top:216px;width:280px;color:#fff;font-size:7.5px;line-height:16px}
.hero-btn{left:58px;top:261px;width:67px;height:29px;border:1.5px solid #fff;color:#fff;font-size:8.5px;display:flex;align-items:center;justify-content:center}
.dots{left:58px;top:307px;display:flex;gap:3px}
.dots i{width:9px;height:9px;border:1px solid #fff;border-radius:50%;display:block}
.dots i.on{background:var(--red)}
.hero-art{left:285px;top:96px;width:370px;height:290px;border-radius:8px 8px 0 0;background:radial-gradient(ellipse at 50% 100%,#6fbf4a 0%,#4d9ed9 28%,rgba(248,113,116,0) 40%),radial-gradient(circle at 50% 40%,#fbbf52 0%,rgba(248,113,116,0) 55%)}

/* Welcome */
.section-title{width:706px;left:0;text-align:center;color:var(--red);font-weight:700}
.welcome-title{top:418px;font-size:18px}
.welcome-sub{left:0;width:706px;text-align:center;top:450px;font-size:8px;color:var(--muted)}
.feature h3{font-weight:400;font-size:13.5px;color:#333}
.feature p{position:absolute;left:47px;top:30px;width:215px;font-size:7px;line-height:13px;color:#444}
.feature .icon{position:absolute;left:0;top:26px}
.feature .more{position:absolute;left:47px;top:72px;width:55px;height:22px;background:var(--red);color:#fff;font-size:7.5px;font-weight:600;display:flex;align-items:center;justify-content:center}
.f-left{left:57px;top:483px;width:270px;height:100px}
.f-right{left:393px;top:483px;width:270px;height:100px}

/* Services */
.services{left:0;top:622px;width:706px;height:274px;background:var(--grey-band)}
.services-title{top:655px;font-size:14px}
.services-rule{left:312px;top:681px;width:82px;height:1.5px;background:var(--red)}
.step{width:150px;text-align:center}
.step .ring{width:78px;height:78px;margin:0 auto;border:1px solid #444;border-radius:50%;display:flex;align-items:center;justify-content:center}
.step .disc{width:70px;height:70px;border-radius:50%;background:var(--dark-icon);display:flex;align-items:center;justify-content:center}
.step.hot .ring{border-color:var(--red)}
.step.hot .disc{background:var(--red)}
.step h4{margin-top:13px;font-weight:400;font-size:10.5px;color:#222}
.step p{margin-top:9px;font-size:7px;line-height:13px;color:#444}

/* Dark band */
.promo{left:0;top:896px;width:706px;height:158px;background:linear-gradient(90deg,#3b3836,#423f3c 50%,#3b3836)}
.promo-title{left:0;width:706px;top:919px;text-align:center;color:#fff;font-size:19.5px;font-weight:600}
.promo-text{left:0;width:706px;top:957px;text-align:center;color:#fff;font-size:8.5px;line-height:17px}
.promo-btn{left:316px;top:1002px;width:74px;height:25px;border:1px solid #fff;color:#fff;font-size:8.5px;font-weight:600;display:flex;align-items:center;justify-content:center;border-radius:2px}

/* Footer */
.footer-map{left:0;top:1054px;width:706px;height:116px;background:linear-gradient(135deg,#f3f2ee,#eceae4 60%,#f1efe9)}
.footer-brand{left:57px;top:1113px}
.info-icon{width:19px;height:19px;border:1px solid #333;border-radius:50%;display:flex;align-items:center;justify-content:center}
.info h5{color:var(--red);font-size:10px;font-weight:600;margin-bottom:7px}
.info p{font-size:8.5px;line-height:14.5px;color:#222}
.bottom-bar{left:0;top:1170px;width:706px;height:30px;background:var(--red);color:#fff;font-size:7.5px;display:flex;align-items:center;padding-left:57px}
.socials{right:34px;top:1176px;display:flex;gap:4px}
.socials i{width:18px;height:18px;border:1px solid #fff;border-radius:50%;display:block}
</style>
</head>
<body>

<header>
  <div class="abs top-rule"></div>
  <div class="abs brand site-brand"><span class="brand-mark"></span>ZELNAR</div>
  <div class="abs search">Search
    <svg width="9" height="9" viewBox="0 0 10 10"><circle cx="4" cy="4" r="3" fill="none" stroke="#444" stroke-width="1.3"/><line x1="6.3" y1="6.3" x2="9" y2="9" stroke="#444" stroke-width="1.3"/></svg>
  </div>
  <div class="abs btn-top btn-later">PAY LATER</div>
  <div class="abs btn-top btn-buy">BUY NOW</div>
  <div class="abs btn-top btn-register">REGISTER</div>
  <nav class="abs nav">
    <span class="active">HOME</span><span>ABOUT US</span><span>PAYMENT INFO</span><span>CUSTOMER PAYMENT</span><span>CONTACT US</span>
  </nav>
</header>

<section>
  <div class="abs hero"></div>
  <div class="abs hero-art" role="img" aria-label="Illustration of a wallet on a globe with coins in several currencies floating above it"></div>
  <h1 class="abs hero-title">PAYMENT PROCESSING<br>COMPANY</h1>
  <p class="abs hero-text">The company is all about flexibility, transparency in personal finance management with the option of instalment payments.</p>
  <div class="abs hero-btn">READ MORE</div>
  <div class="abs dots"><i class="on"></i><i></i><i></i><i></i><i></i></div>
</section>

<section>
  <h2 class="abs section-title welcome-title">WELCOME TO ZELNAR</h2>
  <p class="abs welcome-sub">The company is all about flexibility, transparency in personal finance management with the option of instalment payments</p>

  <div class="abs feature f-left">
    <h3>Merchant Payment</h3>
    <svg class="icon" width="32" height="32" viewBox="0 0 32 32" fill="none" stroke="#ec1f27" stroke-width="1.8">
      <path d="M5 16a11 11 0 0 1 19-7.5"/><path d="M24 3v6h-6"/>
      <path d="M27 16a11 11 0 0 1-19 7.5"/><path d="M8 29v-6h6"/>
      <circle cx="16" cy="16" r="6.5"/>
      <path d="M18 13.5h-3a1.3 1.3 0 0 0 0 2.6h2a1.3 1.3 0 0 1 0 2.6h-3M16 12v8.5" stroke-width="1.3"/>
    </svg>
    <p>Nemo enim ipsam voluptatem quia voluptas sit aspernatur aut odit aut fugit, sed quia consequuntur magni dolores eos qui ratione voluptatem.</p>
    <div class="more">Read More</div>
  </div>

  <div class="abs feature f-right">
    <h3>Outsourced Payment</h3>
    <svg class="icon" width="32" height="36" viewBox="0 0 32 36" fill="none" stroke="#ec1f27" stroke-width="1.6">
      <rect x="9" y="8" width="14" height="18" transform="rotate(-15 16 17)"/>
      <path d="M17.5 13h-3a1.2 1.2 0 0 0 0 2.4h2a1.2 1.2 0 0 1 0 2.4h-3M16 11.5v8" stroke-width="1.2"/>
      <path d="M5 14v18M2 29l3 3 3-3"/><path d="M27 22V4M24 7l3-3 3 3"/>
    </svg>
    <p>Nemo enim ipsam voluptatem quia voluptas sit aspernatur aut odit aut fugit, sed quia consequuntur magni dolores eos qui ratione voluptatem.</p>
    <div class="more">Read More</div>
  </div>
</section>

<section>
  <div class="abs services"></div>
  <h2 class="abs section-title services-title">PAYMENT PROCESSING SERVICES</h2>
  <div class="abs services-rule"></div>

  <svg class="abs" style="left:167px;top:716px" width="52" height="22" viewBox="0 0 52 22" fill="none" stroke="#333" stroke-width="1.8"><path d="M2 12C14 2 32 2 48 18"/><path d="M40 17l8 1 -1-8"/></svg>
  <svg class="abs" style="left:328px;top:758px" width="52" height="22" viewBox="0 0 52 22" fill="none" stroke="#333" stroke-width="1.8"><path d="M2 10C14 20 34 20 48 4"/><path d="M40 4h8v8"/></svg>
  <svg class="abs" style="left:480px;top:716px" width="52" height="22" viewBox="0 0 52 22" fill="none" stroke="#333" stroke-width="1.8"><path d="M2 12C14 2 32 2 48 18"/><path d="M40 17l8 1 -1-8"/></svg>

  <div class="abs step" style="left:47px;top:710px">
    <div class="ring"><div class="disc">
      <svg width="32" height="26" viewBox="0 0 32 26" fill="none" stroke="#fff" stroke-width="2"><rect x="7" y="3" width="22" height="14" rx="2"/><line x1="7" y1="8" x2="29" y2="8"/><path d="M3 12l5 10h8l4-6-6-2"/></svg>
    </div></div>
    <h4>Outsourced Payment</h4>
    <p>The Clearing House uses new tech nology (Blockchain) to settle FX trans actions between participants</p>
  </div>

  <div class="abs step" style="left:198px;top:710px">
    <div class="ring"><div class="disc">
      <svg width="30" height="28" viewBox="0 0 30 28" fill="#fff"><path d="M15 1L2 8h26z"/><rect x="3" y="24" width="24" height="3"/><rect x="5" y="10" width="3" height="12"/><rect x="22" y="10" width="3" height="12"/><text x="15" y="20" text-anchor="middle" font-family="Open Sans,sans-serif" font-weight="700" font-size="11">$</text></svg>
    </div></div>
    <h4>Merchant Payment</h4>
    <p>The Clearing House uses new tech nology (Blockchain) to settle FX trans actions between participants</p>
  </div>

  <div class="abs step hot" style="left:356px;top:710px">
    <div class="ring"><div class="disc">
      <svg width="32" height="32" viewBox="0 0 32 32" fill="none" stroke="#fff" stroke-width="2"><path d="M6 18a10 10 0 0 1 14-12"/><path d="M26 14a10 10 0 0 1-14 12"/><circle cx="20" cy="9" r="4" fill="#fff" stroke="none"/><circle cx="11" cy="22" r="4" fill="#fff" stroke="none"/></svg>
    </div></div>
    <h4>Available Repayment</h4>
    <p>The Clearing House uses new tech nology (Blockchain) to settle FX trans actions between participants</p>
  </div>

  <div class="abs step" style="left:507px;top:710px">
    <div class="ring"><div class="disc">
      <svg width="30" height="26" viewBox="0 0 30 26" fill="#fff"><path d="M3 3h24v15H12l-6 5v-5H3z"/></svg>
    </div></div>
    <h4>Customer Support</h4>
    <p>The Clearing House uses new tech nology (Blockchain) to settle FX trans actions between participants</p>
  </div>
</section>

<section>
  <div class="abs promo" role="img" aria-label="Dimmed illustration of a desk workspace with laptop, calculator, clock and charts"></div>
  <h2 class="abs promo-title">Payment Processing Company From Singapore</h2>
  <p class="abs promo-text">The company is all about flexibility, transparency in personal finance management<br>with the option of instalment payments.</p>
  <div class="abs promo-btn">Read More</div>
</section>

<footer>
  <div class="abs footer-map" role="img" aria-label="Faded road map background"></div>
  <div class="abs brand footer-brand"><span class="brand-mark"></span>ZELNAR</div>

  <div class="abs info-icon" style="left:318px;top:1087px">
    <svg width="10" height="10" viewBox="0 0 10 10"><path d="M2 1l2 0 1 2.5-1.2.8a5 5 0 0 0 2 2l.8-1.2L9 6v2a1 1 0 0 1-1 1A8 8 0 0 1 1 2a1 1 0 0 1 1-1z" fill="#333"/></svg>
  </div>
  <div class="abs info" style="left:350px;top:1087px">
    <h5>Contact:</h5>
    <p>Zelnar,<br>info@zelnar.com<br>+ 180 047 3918</p>
  </div>

  <div class="abs info-icon" style="left:518px;top:1087px">
    <svg width="9" height="11" viewBox="0 0 9 11"><path d="M4.5 10.5S1 6.5 1 4.2a3.5 3.5 0 0 1 7 0c0 2.3-3.5 6.3-3.5 6.3z" fill="none" stroke="#333" stroke-width="1.1"/><circle cx="4.5" cy="4.2" r="1.2" fill="#333"/></svg>
  </div>
  <div class="abs info" style="left:548px;top:1087px">
    <h5>Address:</h5>
    <p>FX Clearing House,<br>2240 Harlow Street West<br>Singapore, MA 02419</p>
  </div>

  <div class="abs bottom-bar">© 2016 Zelnar. All Rights Reserved.</div>
  <div class="abs socials"><i></i><i></i><i></i><i></i><i></i></div>
</footer>

</body>
</html>
```